NEW Wordpress Website Design for a Dynamic Long Term Healthcare Company in Hawaii

I would like a new website design for my current company, Marlow Health Collective, which has two different brands - Marlow Homecare and Marlow Senior Living. You can see the current website at www.marlowhealth-example.com. The website should be built using Wordpress Software and the Framewise theme. The website should have a local Hawaii island/tropical feel, but look professional for healthcare. I'm looking for something fresh, and want the designer to select colors, styles, etc.

In the Header, on all pages, I would like a menu that includes Home Care, Senior Living, Rates, and About Us.
Under each of the Header Menu Titles, I would like these drop downs included:
Home Care (drop down pages)- Nurse Aide Care, 24-Hour Home Care, Skilled Nursing, Lifestyle Aide, Hospice at Home, Bathing & Meal Service.
Senior Living (drop down pages) - Long-Term Stay, Short-Term Stay.
Rates (drop down page) - Rates.
About Us (drop down pages) - Our Mission, Ohana Talk, About Dana Marlow.

In the footer, on all pages, you should include the address: 248 Pueo Lane, Suite 310, Honolulu, HI 96817. Phone number: 808-555-0172
The footer should also include buttons for a page called Learn, Caregiver Jobs, and each of the service page links to include: Nurse Aide Care, 24-Hour Home Care, Skilled Nursing, Lifestyle Aide, Hospice at Home, Bathing & Meal Service.
Please don't take the current website and redesign a few aspects. I'm looking for a completely different look and feel.

Target Market(s)

40-80 year olds

Industry/Entity Type

Long Term Healthcare

Coding

Coded - Design and coding required

Requirements
Should not have
• Our existing website as a template. We are looking for a complete redesign. Thank you.

```html
<!DOCTYPE html>
<html lang="en">
<head>
<meta charset="utf-8">
<title>Marlow Health Collective</title>
<link href="https://fonts.googleapis.com/css2?family=Nunito:ital,wght@0,400;0,500;0,600;1,400;1,500&family=Source+Sans+3:wght@400;500;600&display=swap" rel="stylesheet">
<style>
:root{
  --bg:#f3f3f3;
  --ink:#1d2528;
  --muted:#3c4447;
  --teal:#40dfcf;
  --cyan:#1fdcf0;
  --glow:#8ef0ea;
  --glow-blue:#8ce9f8;
  --line:#c9d3d6;
  --white:#ffffff;
  --coral:#f2756a;
  --sage:#4fa79a;
}
*{box-sizing:border-box;margin:0;padding:0}
html,body{width:1200px;height:2646px;overflow:hidden}
body{background:var(--bg);font-family:'Nunito',sans-serif;color:var(--ink);position:relative}
.glow{position:absolute;border-radius:50%;filter:blur(60px);opacity:.75;pointer-events:none}
.abs{position:absolute}
.heading{font-family:'Source Sans 3',sans-serif;font-weight:500;color:var(--ink)}
.btn{position:absolute;display:flex;align-items:center;justify-content:center;background:var(--teal);color:var(--white);border-radius:14px;font-size:17px;font-family:'Nunito',sans-serif}
.photo{position:absolute;border-radius:18px;overflow:hidden}
.photo-label{position:absolute;left:34px;bottom:34px;font-family:'Source Sans 3',sans-serif;font-size:29px;color:var(--ink)}

/* header */
.brand{position:absolute;top:78px;font-family:'Source Sans 3',sans-serif;font-size:17px;color:var(--ink);display:flex;align-items:center;gap:7px;line-height:1.1}
.brand .dot{width:12px;height:12px;border-radius:3px}
.main-nav{position:absolute;left:346px;top:62px;display:flex;gap:18px;font-size:20px;font-weight:500}
.main-nav span{display:flex;align-items:center;gap:7px}
.contact-btn{left:999px;top:50px;width:151px;height:50px;background:var(--cyan);border-radius:14px;font-size:16px}

/* hero */
.hero-title{left:100px;top:250px;font-size:40px;line-height:58px;letter-spacing:.5px}
.hero-copy{left:100px;top:366px;width:600px;font-size:16px;line-height:23px;color:var(--muted)}
.hero-copy p+p{margin-top:21px}

.section-title{font-size:27px}
.section-copy{font-size:12.5px;line-height:19px;color:var(--muted);margin-top:18px}

/* form */
.form-card{position:absolute;left:600px;top:1673px;width:552px;height:386px;background:var(--white);border-radius:18px;padding:34px 30px}
.field-label{position:absolute;font-size:12px;color:var(--ink)}
.field{position:absolute;border:1px solid var(--line);border-radius:6px;height:34px;font-size:10px;color:#a4abae;padding:10px 16px}
.check{position:absolute;left:30px;top:326px;display:flex;align-items:center;gap:9px;font-size:10px}
.check i{width:16px;height:16px;border:1px solid var(--line);display:block}

.quote{position:absolute;left:0;top:2170px;width:1200px;text-align:center;font-style:italic;font-size:26px;font-weight:500}

.footer-brand{position:absolute;top:2320px;font-family:'Source Sans 3',sans-serif;font-size:22px;display:flex;align-items:center;gap:9px;color:var(--ink)}
.footer-brand .dot{width:16px;height:16px;border-radius:4px}
.footer-nav{position:absolute;right:48px;top:2445px;display:flex;gap:20px;font-size:11.5px;font-weight:500}
.contact-line{position:absolute;left:68px;display:flex;align-items:center;gap:10px;font-size:11.5px;color:var(--muted)}
.social{position:absolute;top:2528px;width:28px;height:28px;border-radius:50%;background:var(--ink)}
.copyright{position:absolute;left:75px;top:2594px;font-size:11.5px}
</style>
</head>
<body>

<!-- ambient glows -->
<div class="glow" style="left:130px;top:-60px;width:700px;height:160px;background:var(--glow)"></div>
<div class="glow" style="left:60px;top:220px;width:380px;height:90px;background:var(--glow)"></div>
<div class="glow" style="left:-80px;top:540px;width:260px;height:200px;background:var(--glow-blue)"></div>
<div class="glow" style="left:950px;top:420px;width:320px;height:300px;background:var(--glow-blue)"></div>
<div class="glow" style="left:1040px;top:860px;width:240px;height:260px;background:var(--glow)"></div>
<div class="glow" style="left:-60px;top:1180px;width:200px;height:220px;background:var(--glow-blue)"></div>
<div class="glow" style="left:20px;top:1880px;width:220px;height:200px;background:var(--glow)"></div>
<div class="glow" style="left:200px;top:2130px;width:720px;height:90px;background:var(--glow)"></div>
<div class="glow" style="left:1000px;top:2230px;width:260px;height:230px;background:var(--glow-blue)"></div>
<div class="glow" style="left:-100px;top:2560px;width:1400px;height:160px;background:var(--glow-blue)"></div>

<!-- header -->
<header>
  <div class="brand" style="left:60px"><span class="dot" style="background:var(--coral)"></span>Marlow<br>Homecare</div>
  <div class="brand" style="left:170px"><span class="dot" style="background:var(--sage)"></span>Marlow<br>Senior Living</div>
  <nav class="main-nav">
    <span>Home Care <svg width="16" height="10" viewBox="0 0 16 10"><path d="M1 2l7 6 7-6" fill="none" stroke="#1d2528" stroke-width="1.8"/></svg></span>
    <span>Senior Living <svg width="16" height="10" viewBox="0 0 16 10"><path d="M1 2l7 6 7-6" fill="none" stroke="#1d2528" stroke-width="1.8"/></svg></span>
    <span>Rates <svg width="16" height="10" viewBox="0 0 16 10"><path d="M1 2l7 6 7-6" fill="none" stroke="#1d2528" stroke-width="1.8"/></svg></span>
    <span>About Us <svg width="16" height="10" viewBox="0 0 16 10"><path d="M1 2l7 6 7-6" fill="none" stroke="#1d2528" stroke-width="1.8"/></svg></span>
  </nav>
  <div class="btn contact-btn">Contact Us</div>
</header>

<!-- hero -->
<section class="hero">
  <h1 class="heading abs hero-title">HAWAII'S CHOICE<br>HOMECARE &amp; SENIOR LIVING</h1>
  <div class="abs hero-copy">
    <p>Marlow Homecare provides a variety of professional in-home health care services throughout the entire island of Oahu.</p>
    <p>Marlow Senior Living, a beautiful Adult Residential Care Home, is located on the windward side of Oahu in Kailua.</p>
  </div>
  <div class="btn" style="left:100px;top:505px;width:257px;height:50px">Get Started</div>
  <div class="photo" role="img" aria-label="Portrait of a smiling nurse in a white uniform with a stethoscope" style="left:731px;top:187px;width:351px;height:469px;border-radius:16px;background:linear-gradient(160deg,#d9d4cf,#b9a89c 55%,#e6e2dd)"></div>
</section>

<!-- home care -->
<section>
  <div class="photo" role="img" aria-label="Caregiver helping an older man in a bedroom at home" style="left:50px;top:730px;width:550px;height:390px;background:linear-gradient(165deg,#c9d98a,#8fd3a8 55%,#5fd8bf)">
    <div class="photo-label">Home Care</div>
  </div>
  <div class="abs" style="left:629px;top:754px;width:410px">
    <h2 class="heading section-title">Professional Care In Your Home</h2>
    <p class="section-copy">Marlow Homecare understands that every person's care journey is unique. We tailor our in-home services to meet the diverse nurturing experience of professional quality care and safety within the comfort and convenience of your own home.</p>
  </div>
  <div class="btn" style="left:629px;top:928px;width:257px;height:50px">Schedule care assessment</div>
</section>

<!-- senior living -->
<section>
  <div class="abs" style="left:168px;top:1228px;width:410px">
    <h2 class="heading section-title">Trusted Care In Our Home</h2>
    <p class="section-copy">Marlow Senior Living creates a warm, supportive, and enriching care home environment where seniors can thrive in their golden years. We provide residential care that promotes well-being, connection, and dignity of each individual.</p>
  </div>
  <div class="btn" style="left:168px;top:1403px;width:257px;height:50px">Schedule Tour</div>
  <div class="photo" role="img" aria-label="Seniors exercising with light weights in a bright living room with a trainer" style="left:600px;top:1204px;width:549px;height:391px;background:linear-gradient(160deg,#b9b46a,#8fc79a 50%,#6fcfb6)">
    <div class="photo-label">Senior Living</div>
  </div>
</section>

<!-- consultation -->
<section>
  <h2 class="heading abs" style="left:50px;top:1640px;font-size:34px;line-height:50px">Schedule a complimentary<br>Care Consultation</h2>
  <form class="form-card">
    <span class="field-label" style="left:30px;top:38px">Name</span>
    <div class="field" style="left:30px;top:57px;width:234px">Enter your name</div>
    <span class="field-label" style="left:285px;top:38px">Email</span>
    <div class="field" style="left:285px;top:57px;width:234px">example: jane@example.com</div>
    <span class="field-label" style="left:30px;top:99px">Phone Number</span>
    <div class="field" style="left:30px;top:118px;width:234px">083xxxxxxx</div>
    <span class="field-label" style="left:285px;top:99px">How we can help?</span>
    <div class="field" style="left:285px;top:118px;width:234px;color:var(--ink);display:flex;justify-content:space-between;align-items:center;padding:0 16px">Choose <svg width="12" height="8" viewBox="0 0 12 8"><path d="M1 1l5 5 5-5" fill="none" stroke="#1d2528" stroke-width="1.4"/></svg></div>
    <span class="field-label" style="left:30px;top:160px">How did you hear about us?</span>
    <div class="field" style="left:30px;top:179px;width:489px;height:113px;padding-top:48px">Write here...</div>
    <div class="check"><i></i>I want to receive email about the schedule complimentary</div>
    <div class="btn" style="left:360px;top:300px;width:150px;height:50px">Set Schedule</div>
  </form>
</section>

<p class="quote">Caregiving is a series of small acts of care that alter the course of someone's life."</p>

<!-- footer -->
<footer>
  <div class="footer-brand" style="left:334px"><span class="dot" style="background:var(--coral)"></span>Marlow Homecare</div>
  <div class="footer-brand" style="left:560px"><span class="dot" style="background:var(--ink)"></span>Marlow Health Collective</div>
  <div class="footer-brand" style="left:840px"><span class="dot" style="background:var(--sage)"></span>Marlow Senior Living</div>

  <nav class="footer-nav"><span>HOME PAGE</span><span>CONTACT</span><span>LEARN</span><span>CAREGIVER JOBS</span><span>PRIVACY POLICY</span></nav>

  <div class="contact-line" style="top:2494px">
    <svg width="16" height="18" viewBox="0 0 16 18"><path d="M8 17s6-6 6-10A6 6 0 0 0 2 7c0 4 6 10 6 10z" fill="none" stroke="#1d2528" stroke-width="1.4"/><circle cx="8" cy="7" r="2.2" fill="none" stroke="#1d2528" stroke-width="1.4"/></svg>
    248 Pueo Lane, Suite 310, Honolulu, HI 96817
  </div>
  <div class="contact-line" style="top:2530px">
    <svg width="18" height="18" viewBox="0 0 18 18"><path d="M4 1.5l3 3.5-1.6 2a10 10 0 0 0 5.6 5.6l2-1.6 3.5 3-1.5 2.5C8 16 2 10 1.5 3z" fill="none" stroke="#1d2528" stroke-width="1.3" stroke-linejoin="round"/></svg>
    808-555-0172
  </div>

  <span class="social" style="left:969px"></span>
  <span class="social" style="left:1019px"></span>
  <span class="social" style="left:1069px"></span>
  <span class="social" style="left:1119px"></span>

  <p class="copyright">© 2023 Marlow Health Collective. All Rights Reserved</p>
</footer>

</body>
</html>
```